Business Card Design

Business Card for professional consulting firm working with large financial institutions.

Target Market(s)

Executive buyers

Industry/Entity Type

Banking

Contact Information for Business Card

Mild creativity wanted. Not boring, but do elaborate artwork.

Font styles to use
Serif
Sans Serif

Colors

Designer to choose colors to be used in the design.

Requirements
Must have
• Standard business card features - company name, individual name, telephone, website, email, locations.
Nice to have
• Two colors
Should not have
• too many colors, fancy printing, cartoons.

```html
<!DOCTYPE html>
<html lang="en">
<head>
<meta charset="utf-8">
<title>Northvale Advisory – Business Card</title>
<link rel="stylesheet" href="https://fonts.googleapis.com/css2?family=Bebas+Neue&family=Work+Sans:wght@400;500&display=swap">
<style>
  :root {
    --backdrop: #1f1f1f;
    --card: #141414;
    --card-edge: #1b1b1b;
    --ink: #f2f2f2;
    --ink-soft: #c9c9c9;
    --rule: #d0d0d0;
  }
  * { margin: 0; padding: 0; box-sizing: border-box; }
  html, body {
    width: 1200px; height: 900px; overflow: hidden;
    background: var(--backdrop);
  }
  .sheet {
    width: 1200px; height: 900px;
    display: flex; flex-direction: column;
    align-items: center; justify-content: center; gap: 44px;
  }
  .card {
    position: relative;
    width: 560px; height: 320px;
    background: linear-gradient(135deg, var(--card) 0%, var(--card-edge) 100%);
    color: var(--ink);
    font-family: "Work Sans", sans-serif;
  }
  .card-front {
    display: flex; align-items: center; justify-content: center;
  }
  .brand {
    display: flex; align-items: center; gap: 14px;
    font-family: "Work Sans", sans-serif;
    font-weight: 400; font-size: 38px; letter-spacing: 0.5px;
    color: var(--ink);
  }
  .brand-dot {
    width: 14px; height: 14px; border-radius: 50%;
    background: var(--ink);
  }
  .identity {
    position: absolute; left: 40px; top: 102px; width: 200px;
    text-align: right;
  }
  .person-name {
    font-family: "Bebas Neue", sans-serif;
    font-size: 46px; line-height: 1; color: var(--ink-soft);
    letter-spacing: 0.5px;
  }
  .person-role {
    font-size: 16px; color: var(--ink); margin-top: 2px;
  }
  .divider {
    position: absolute; left: 270px; top: 108px;
    width: 2px; height: 64px; background: var(--rule);
  }
  .contact-list {
    position: absolute; left: 296px; top: 112px;
    list-style: none; font-size: 16px; line-height: 20px;
  }
  .contact-list li { display: flex; align-items: center; gap: 10px; }
  .contact-list svg { width: 11px; height: 11px; flex: none; }
  .address {
    position: absolute; left: 70px; top: 250px;
    font-size: 17px; color: var(--ink);
  }
</style>
</head>
<body>
<main class="sheet">
  <section class="card card-front" aria-label="Card front">
    <div class="brand"><span class="brand-dot"></span>Northvale Advisory</div>
  </section>

  <section class="card card-back" aria-label="Card back">
    <div class="identity">
      <h1 class="person-name">Daniel Hart</h1>
      <p class="person-role">Director</p>
    </div>
    <div class="divider"></div>
    <ul class="contact-list">
      <li>
        <svg viewBox="0 0 12 12" aria-hidden="true"><path d="M3 1l2 2.5-1.2 1.2a7 7 0 0 0 3.5 3.5L8.5 7 11 9l-1.2 2C5.5 11 1 6.5 1 2.2z" fill="none" stroke="#ddd" stroke-width="1"/></svg>
        +330 2460-5172
      </li>
      <li>
        <svg viewBox="0 0 12 12" aria-hidden="true"><rect x="1" y="2.5" width="10" height="7" fill="none" stroke="#ddd"/><path d="M1 2.5l5 4 5-4" fill="none" stroke="#ddd"/></svg>
        info@northvaleadvisory.com
      </li>
      <li>
        <svg viewBox="0 0 12 12" aria-hidden="true"><circle cx="6" cy="6" r="5" fill="none" stroke="#ddd"/><ellipse cx="6" cy="6" rx="2.2" ry="5" fill="none" stroke="#ddd"/><path d="M1 6h10" stroke="#ddd"/></svg>
        www.northvaleadvisory.com
      </li>
    </ul>
    <p class="address">48 Calder Lane, Ashbury VIC 3712</p>
  </section>
</main>
</body>
</html>
```